brovlanepass.net

Develop a website for brolanepass.net will be a site to sell tickets for concerts, shows, shows, theaters and others. I need a web design easy view, very easy to use and accumulate events by date. The aim is to develop the site was connected to a complex system that is already developed. (Important this page to a robust system was connected via links the idea is to develop only the front view)
Updates

Reason: I need more designs yet we have not made the decision

Target Market(s)

millennials, adults, who want to enjoy concerts and shows

Industry/Entity Type

Event

Number of Pages Required

5+ page

Colors
1b1b1b
aaaaaa
ffffff

Requirements
Must have
• Easy Vista, accumulation of upcoming events, past events. The tabs should have are: 1 Start: In this part of upcoming events occur. You could put a banner on the top and down the events by date. 2. How to order: page with instructions on how to purchase tickets 3. About Us: The company history 4. Contact: Phones and template for contact by mail 5. Our policies: shopping 6. Notice Privacy: Privacy Notice Copoy 7. Centers Sale: physical places where they can purchase tickets Promoters 8. access: Link to a template
Nice to have
• as you can see p www.quimbarostage.net or farunda.net or farunda.org or gallowmerk.net (important this page to a robust system was connected via links the idea is to develop only the front view)
Should not have
• Many things Tangled

```html
<!DOCTYPE html>
<html lang="en">
<head>
<meta charset="utf-8">
<title>Brovlanepass – Upcoming Events</title>
<link rel="stylesheet" href="https://fonts.googleapis.com/css2?family=Open+Sans:wght@400;600;700&family=Roboto+Condensed:wght@400;700&display=swap">
<style>
:root{
  --ink:#1b1b1b;
  --page:#0b0b0b;
  --bar:#111111;
  --footer:#1d1d1d;
  --copy:#141414;
  --grey:#aaaaaa;
  --white:#ffffff;
  --muted:#d6d6d6;
  --line:#2e2e2e;
}
*{box-sizing:border-box;margin:0;padding:0}
html,body{width:1200px;height:2416px;overflow:hidden;background:var(--page);color:var(--white);font-family:"Open Sans",sans-serif}
a{color:inherit;text-decoration:none}

/* hero */
.hero{position:relative;height:552px;overflow:hidden}
.hero-photo{position:absolute;inset:0;background:
  radial-gradient(ellipse 30% 40% at 50% 30%,rgba(255,220,200,.85),transparent 70%),
  radial-gradient(ellipse 55% 55% at 50% 35%,#d2482c 0%,#7a1a12 45%,transparent 80%),
  linear-gradient(180deg,#2a0a06 0%,#3d0f08 45%,#120604 80%,#050202 100%)}
.hero-shade{position:absolute;left:0;right:0;bottom:0;height:200px;background:linear-gradient(180deg,transparent,rgba(0,0,0,.85))}
.topbar{position:absolute;left:0;right:0;top:0;height:60px;border-bottom:1px solid rgba(255,255,255,.18);display:flex;align-items:center;padding:0 98px}
.social-top{display:flex;gap:15px}
.social-top span{width:11px;height:11px;border-radius:50%;background:var(--white)}
.search{margin-left:40px;width:174px;height:32px;border-radius:16px;background:rgba(20,20,20,.85);display:flex;align-items:center;justify-content:space-between;padding:0 16px;font-size:11px;color:var(--muted)}
.login{margin-left:auto;display:flex;align-items:center;gap:10px;font-size:13px;font-weight:600;letter-spacing:.3px}
.brand{position:absolute;left:98px;top:80px;font-size:30px;font-weight:700;letter-spacing:.5px}
.nav{position:absolute;right:98px;top:82px;display:flex;gap:26px;font-size:13.5px}
.nav a{position:relative;padding-bottom:10px}
.nav a.active::after{content:"";position:absolute;left:50%;transform:translateX(-50%);bottom:0;width:26px;height:2px;background:var(--white)}
.dots{position:absolute;left:50%;top:505px;transform:translateX(-50%);display:flex;gap:7px}
.dots span{width:12px;height:12px;border-radius:50%;border:1.5px solid var(--white)}
.dots span.on{background:var(--white)}

/* events */
.events{height:1537px;background:var(--page);padding-top:55px}
.events-title{font-family:"Roboto Condensed",sans-serif;font-size:26px;font-weight:400;text-align:center;letter-spacing:.3px}
.event-grid{margin:52px auto 0;width:1004px;display:grid;grid-template-columns:repeat(3,317px);column-gap:26px;row-gap:28px}
.event-card{position:relative;height:398px;overflow:hidden;border:1px solid #262626}
.event-photo{position:absolute;inset:0}
.event-card::after{content:"";position:absolute;left:0;right:0;bottom:0;height:60%;background:linear-gradient(180deg,transparent,rgba(0,0,0,.55))}
.event-body{position:absolute;z-index:1;left:18px;top:240px;right:70px}
.event-name{font-size:13.5px;font-weight:700;line-height:20px;text-transform:uppercase}
.event-text{margin-top:6px;font-size:11.5px;line-height:20px;color:var(--white)}
.book-btn{position:absolute;z-index:1;left:18px;top:330px;width:104px;height:38px;border-radius:8px;background:var(--white);color:var(--ink);font-size:11.5px;font-weight:600;display:flex;align-items:center;justify-content:center}
.event-date{position:absolute;z-index:1;right:0;bottom:0;width:56px;height:95px;background:rgba(170,170,170,.82);text-align:center;font-weight:700}
.event-date .day{display:block;margin-top:6px;font-size:15px;line-height:18px}
.event-date .mon,.event-date .yr{display:block;font-size:11.5px;line-height:19px}
.event-date .time{position:absolute;left:0;right:0;bottom:0;height:22px;background:rgba(140,140,140,.9);font-size:10px;font-style:italic;font-weight:400;line-height:22px;color:#222}
.view-more{display:flex;margin:55px auto 0;width:129px;height:44px;border-radius:8px;background:#1f1f1f;box-shadow:0 2px 6px rgba(0,0,0,.6);align-items:center;justify-content:center;font-size:13px;font-weight:700}

.p1{background:radial-gradient(circle at 45% 10%,#fff2b0,transparent 30%),linear-gradient(180deg,#e0a024,#b6620e 55%,#3a1a05)}
.p2{background:radial-gradient(circle at 50% 15%,#f2d8ff,transparent 28%),linear-gradient(180deg,#a53ed1,#6d1c9a 55%,#25063a)}
.p3{background:radial-gradient(circle at 40% 10%,#ffd27a,transparent 30%),linear-gradient(180deg,#c24a6a,#5a2aa0 55%,#101a6a)}
.p4{background:linear-gradient(180deg,#12244a,#4a1e3a 35%,#6a3a52 55%,#111625)}
.p5{background:linear-gradient(160deg,#4a3a34,#7a5a48 45%,#2a2222)}
.p6{background:radial-gradient(circle at 45% 25%,#d7c7a0,transparent 25%),linear-gradient(180deg,#2a2a30,#4a2a22 55%,#1a0f0c)}
.p7{background:radial-gradient(circle at 20% 45%,#ffe0a8,transparent 30%),linear-gradient(180deg,#2a2a36,#6a3a22 55%,#181210)}
.p8{background:radial-gradient(circle at 50% 35%,#e6eefa,transparent 35%),linear-gradient(180deg,#2a4aa6,#5a78c2 45%,#1a1f3a)}
.p9{background:linear-gradient(180deg,#3a2630,#b3141e 35%,#7a0a12 65%,#2a0606)}

/* footer */
.site-footer{position:relative;height:279px;background:var(--footer)}
.f-col{position:absolute;top:58px}
.f-head{font-family:"Roboto Condensed",sans-serif;font-size:18px;font-weight:400;letter-spacing:.2px}
.f-list{list-style:none;margin-top:21px}
.f-list li{height:33.5px;font-size:12px;display:flex;align-items:flex-start;gap:14px;color:var(--muted)}
.f-list li .chev{font-size:10px;color:var(--white)}
.contact li{gap:14px;height:auto;line-height:20px;margin-bottom:12px}
.contact svg{flex:none;margin-top:2px}
.social li{align-items:center;height:40px;gap:15px}
.ring{width:32px;height:32px;border-radius:50%;border:1.5px solid var(--white);display:flex;align-items:center;justify-content:center}
.ring i{width:8px;height:8px;border-radius:50%;background:var(--white)}
.copyright{height:48px;background:var(--copy);display:flex;align-items:center;justify-content:center;font-size:11.5px;color:var(--muted)}
</style>
</head>
<body>

<header class="hero">
  <div class="hero-photo" role="img" aria-label="Concert crowd raising hands before a stage lit by bright red and orange spotlights"></div>
  <div class="hero-shade"></div>

  <div class="topbar">
    <div class="social-top" aria-label="Social links"><span></span><span></span><span></span><span></span><span></span></div>
    <div class="search">Search..... 
      <svg width="11" height="11" viewBox="0 0 12 12"><circle cx="5" cy="5" r="3.8" fill="none" stroke="#fff" stroke-width="1.6"/><path d="M8 8l3 3" stroke="#fff" stroke-width="1.8"/></svg>
    </div>
    <a class="login" href="#">
      <svg width="12" height="13" viewBox="0 0 12 13"><circle cx="6" cy="3.5" r="3" fill="#fff"/><path d="M0 13c0-4 2.5-6 6-6s6 2 6 6z" fill="#fff"/></svg>
      LOG IN
    </a>
  </div>

  <a class="brand" href="#">BROVLANEPASS</a>
  <nav class="nav">
    <a class="active" href="#">Home</a>
    <a href="#">How to Order</a>
    <a href="#">About us</a>
    <a href="#">Contact us</a>
    <a href="#">Policies</a>
    <a href="#">Privacy</a>
    <a href="#">Center Sale</a>
    <a href="#">Access</a>
  </nav>

  <div class="dots"><span class="on"></span><span></span><span></span><span></span><span></span><span></span><span></span></div>
</header>

<main class="events">
  <h1 class="events-title">UPCOMING EVENTS</h1>
  <div class="event-grid">

    <article class="event-card"><div class="event-photo p1" role="img" aria-label="Amber stage lights over a concert crowd"></div>
      <div class="event-body"><h2 class="event-name">Quis nostrum exercitationem ullam corporis</h2><p class="event-text">But I must explain to you how all this is taken idea of denouncing pleasure</p></div>
      <a class="book-btn" href="#">Book Tickets</a>
      <div class="event-date"><span class="day">10</span><span class="mon">NOV</span><span class="yr">2017</span><span class="time">01:98</span></div></article>

    <article class="event-card"><div class="event-photo p2" role="img" aria-label="Purple-lit concert with crowd raising hands"></div>
      <div class="event-body"><h2 class="event-name">Quis nostrum exercitationem ullam corporis</h2><p class="event-text">But I must explain to you how all this is taken idea of denouncing pleasure</p></div>
      <a class="book-btn" href="#">Book Tickets</a>
      <div class="event-date"><span class="day">08</span><span class="mon">OCT</span><span class="yr">2017</span><span class="time">01:98</span></div></article>

    <article class="event-card"><div class="event-photo p3" role="img" aria-label="Band on stage under warm spotlights and blue haze"></div>
      <div class="event-body"><h2 class="event-name">Quis nostrum exercitationem ullam corporis</h2><p class="event-text">But I must explain to you how all this is taken idea of denouncing pleasure</p></div>
      <a class="book-btn" href="#">Book Tickets</a>
      <div class="event-date"><span class="day">10</span><span class="mon">NOV</span><span class="yr">2017</span><span class="time">01:98</span></div></article>

    <article class="event-card"><div class="event-photo p4" role="img" aria-label="Theatre stage with red draped curtain and seating"></div>
      <div class="event-body"><h2 class="event-name">Quis nostrum exercitationem ullam corporis</h2><p class="event-text">But I must explain to you how all this is taken idea of denouncing pleasure</p></div>
      <a class="book-btn" href="#">Book Tickets</a>
      <div class="event-date"><span class="day">10</span><span class="mon">NOV</span><span class="yr">2017</span><span class="time">01:98</span></div></article>

    <article class="event-card"><div class="event-photo p5" role="img" aria-label="Audience laughing together at a show"></div>
      <div class="event-body"><h2 class="event-name">Quis nostrum exercitationem ullam corporis</h2><p class="event-text">But I must explain to you how all this is taken idea of denouncing pleasure</p></div>
      <a class="book-btn" href="#">Book Tickets</a>
      <div class="event-date"><span class="day">08</span><span class="mon">OCT</span><span class="yr">2017</span><span class="time">01:98</span></div></article>

    <article class="event-card"><div class="event-photo p6" role="img" aria-label="Performer on an ornate theatre stage with a screen"></div>
      <div class="event-body"><h2 class="event-name">Quis nostrum exercitationem ullam corporis</h2><p class="event-text">But I must explain to you how all this is taken idea of denouncing pleasure</p></div>
      <a class="book-btn" href="#">Book Tickets</a>
      <div class="event-date"><span class="day">10</span><span class="mon">NOV</span><span class="yr">2017</span><span class="time">01:98</span></div></article>

    <article class="event-card"><div class="event-photo p7" role="img" aria-label="Arena concert with light beams over the crowd"></div>
      <div class="event-body"><h2 class="event-name">Quis nostrum exercitationem ullam corporis</h2><p class="event-text">But I must explain to you how all this is taken idea of denouncing pleasure</p></div>
      <a class="book-btn" href="#">Book Tickets</a>
      <div class="event-date"><span class="day">10</span><span class="mon">NOV</span><span class="yr">2017</span><span class="time">01:98</span></div></article>

    <article class="event-card"><div class="event-photo p8" role="img" aria-label="Blue hazy stage lights at a live show"></div>
      <div class="event-body"><h2 class="event-name">Quis nostrum exercitationem ullam corporis</h2><p class="event-text">But I must explain to you how all this is taken idea of denouncing pleasure</p></div>
      <a class="book-btn" href="#">Book Tickets</a>
      <div class="event-date"><span class="day">08</span><span class="mon">OCT</span><span class="yr">2017</span><span class="time">01:98</span></div></article>

    <article class="event-card"><div class="event-photo p9" role="img" aria-label="Theatre hall with red stage curtain and red seats"></div>
      <div class="event-body"><h2 class="event-name">Quis nostrum exercitationem ullam corporis</h2><p class="event-text">But I must explain to you how all this is taken idea of denouncing pleasure</p></div>
      <a class="book-btn" href="#">Book Tickets</a>
      <div class="event-date"><span class="day">10</span><span class="mon">NOV</span><span class="yr">2017</span><span class="time">01:98</span></div></article>

  </div>
  <a class="view-more" href="#">VIEW MORE</a>
</main>

<footer class="site-footer">
  <div class="f-col" style="left:100px">
    <h3 class="f-head">CONTACT US</h3>
    <ul class="f-list contact">
      <li><svg width="14" height="18" viewBox="0 0 14 18"><path d="M7 1a6 6 0 0 0-6 6c0 4.5 6 10 6 10s6-5.5 6-10a6 6 0 0 0-6-6z" fill="none" stroke="#fff" stroke-width="1.4"/><circle cx="7" cy="7" r="2" fill="none" stroke="#fff" stroke-width="1.4"/></svg><span>120,Avenue Brovlanepass<br>Lorem ipsum</span></li>
      <li><svg width="15" height="15" viewBox="0 0 16 16"><path d="M3 1l3 3-2 2c1 2.5 3.5 5 6 6l2-2 3 3-2 2C7 15 1 9 1 3z" fill="none" stroke="#fff" stroke-width="1.3"/></svg><span>Phone : (555)-210-4876</span></li>
      <li><svg width="16" height="12" viewBox="0 0 16 12"><rect x="1" y="1" width="14" height="10" fill="none" stroke="#fff" stroke-width="1.3"/><path d="M1 1l7 6 7-6" fill="none" stroke="#fff" stroke-width="1.3"/></svg><span>Email : info@brovlanepass.net</span></li>
    </ul>
  </div>

  <div class="f-col" style="left:390px">
    <h3 class="f-head">QUICK LINKS</h3>
    <ul class="f-list">
      <li><span class="chev">»</span>Home</li>
      <li><span class="chev">»</span>How to Order</li>
      <li><span class="chev">»</span>About us</li>
      <li><span class="chev">»</span>Contact us</li>
    </ul>
  </div>

  <div class="f-col" style="left:588px">
    <h3 class="f-head">OTHER LINKS</h3>
    <ul class="f-list">
      <li><span class="chev">»</span>Policies</li>
      <li><span class="chev">»</span>Privacy</li>
      <li><span class="chev">»</span>Center Sale</li>
      <li><span class="chev">»</span>Access</li>
    </ul>
  </div>

  <div class="f-col" style="left:783px;top:79px">
    <ul class="f-list">
      <li><span class="chev">»</span>FAQ</li>
      <li><span class="chev">»</span>I Love My Ticket</li>
      <li><span class="chev">»</span>Terugbetaling</li>
      <li><span class="chev">»</span>Disclaimer</li>
    </ul>
  </div>

  <div class="f-col" style="left:967px">
    <h3 class="f-head">STAY CONNECTED</h3>
    <ul class="f-list social">
      <li><span class="ring"><i></i></span>Friendwall</li>
      <li><span class="ring"><i></i></span>Chirpline</li>
      <li><span class="ring"><i></i></span>Vidstream</li>
    </ul>
  </div>
</footer>

<div class="copyright">@copyright 2017 Brovlanepass.All Rights Reserved</div>

</body>
</html>
```